Mental Health care Company in Washington DC

We are a new mental health care services provider in Washington DC. Please look at these sites.
https://brightwaterfamilysupport.com
https://www.quietharborinc.com
https://willowgate-dc.org/
https://www.tidepathdc.com
https://www.thelanternofdc.com

```html
<!DOCTYPE html>
<html lang="en">
<head>
<meta charset="utf-8">
<title>Calder Health Services</title>
<link href="https://fonts.googleapis.com/css2?family=Poppins:wght@400;500;600;700;800&family=Work+Sans:wght@400;500;600&display=swap" rel="stylesheet">
<style>
:root{
  --navy:#0b1c3d;
  --teal:#a3dade;
  --orange:#f5a260;
  --ink:#1d2433;
  --muted:#6a6f7a;
  --grey:#e6e4e6;
  --white:#ffffff;
}
*{box-sizing:border-box;margin:0;padding:0}
html,body{width:1200px;height:4071px;overflow:hidden}
body{font-family:"Work Sans",sans-serif;color:var(--ink);background:var(--white);position:relative}
.abs{position:absolute}
.heading{font-family:"Poppins",sans-serif;font-weight:700}

/* top bar */
.topbar{top:0;left:0;width:1200px;height:44px;background:var(--navy);color:var(--white)}
.topbar .dot{position:absolute;top:15px;width:15px;height:15px;border-radius:50%;background:var(--white)}
.topbar .help{position:absolute;right:52px;top:12px;font-size:15px;display:flex;align-items:center;gap:10px}
.topbar .help b{font-weight:600}

/* header */
.header{top:44px;left:0;width:1200px;height:121px;background:var(--white);border-bottom:5px solid var(--navy)}
.brand{position:absolute;left:172px;top:22px}
.brand .name{font-family:"Poppins",sans-serif;font-weight:500;font-size:46px;color:var(--navy);line-height:1;letter-spacing:-1px}
.brand .sub{font-family:"Poppins",sans-serif;font-size:15px;letter-spacing:9px;color:var(--muted);margin-top:4px;padding-left:46px}
.nav{position:absolute;left:536px;top:56px;display:flex;gap:43px;font-size:19px;color:var(--muted)}
.nav .search{width:12px;height:12px;border:2px solid var(--muted);border-radius:50%;margin-top:5px}

/* hero */
.hero{top:171px;left:0;width:1200px;height:640px;background:linear-gradient(100deg,#6f6259 0%,#8b7b6d 35%,#5d6f72 65%,#3d6870 100%)}
.hero h1{position:absolute;left:161px;top:160px;font-size:63px;line-height:61px;color:var(--white);font-weight:800;width:620px}
.hero p{position:absolute;left:161px;top:308px;width:570px;font-family:"Poppins",sans-serif;font-size:13.5px;line-height:24px;color:var(--white);font-weight:500}
.btn{position:absolute;height:32px;border-radius:16px;font-family:"Poppins",sans-serif;font-weight:600;font-size:14px;color:var(--navy);display:flex;align-items:center;justify-content:center}
.btn.teal{background:var(--teal)}
.btn.orange{background:var(--orange)}
.btn.outline{border:2px solid var(--white);color:var(--white);letter-spacing:1px;font-size:14px}

/* welcome */
.welcome{top:798px;left:0;width:1200px;height:275px;background:var(--teal);text-align:center;color:var(--white)}
.welcome h2{margin-top:70px;font-size:44px;letter-spacing:.5px;font-weight:600}
.welcome p{margin:22px auto 0;width:860px;font-family:"Poppins",sans-serif;font-size:16px;line-height:27px;font-weight:500}

/* stories */
.stories{top:1073px;left:0;width:1200px;height:540px;background:linear-gradient(90deg,#1e1d1c 0%,#4a3f37 30%,#6a5a4e 55%,#2a2826 85%,#111 100%)}
.stories h2{position:absolute;left:161px;top:272px;font-size:53px;color:var(--white);font-weight:700}
.stories p{position:absolute;left:161px;top:343px;width:570px;font-family:"Poppins",sans-serif;font-size:13.5px;line-height:24px;color:var(--white);font-weight:500}

.edge{position:absolute;left:0;width:1200px}

/* services */
.services-title{top:1672px;left:0;width:1200px;text-align:center}
.services-title h2{display:inline-block;font-size:46px;color:var(--navy);font-weight:700;border-bottom:4px solid var(--navy);line-height:52px}
.card{position:absolute;top:1794px;width:205px;height:361px;background:var(--white);border-radius:22px;box-shadow:0 2px 10px rgba(0,0,0,.28);text-align:center}
.card .icon{position:absolute;left:76px;top:20px;width:52px;height:52px}
.card .num{position:absolute;right:20px;top:36px;font-family:"Poppins",sans-serif;font-weight:700;font-size:24px;color:#c9ccd2}
.card h3{position:absolute;top:86px;left:0;width:100%;font-family:"Poppins",sans-serif;font-weight:500;font-size:19px;color:var(--navy)}
.card p{position:absolute;top:130px;left:32px;width:141px;font-size:10.5px;line-height:13.5px;color:var(--muted)}
.card .more{position:absolute;left:47px;top:296px;width:110px;height:24px;border-radius:12px;background:var(--orange);color:var(--white);font-size:10px;font-weight:600;display:flex;align-items:center;justify-content:center}

/* team */
.team{top:2245px;left:0;width:1200px;height:720px;background:linear-gradient(110deg,#d5eff2 0%,#c4e6ec 45%,#b5dde6 100%)}
.team .ph{position:absolute;width:208px;height:208px}
.team .divider{position:absolute;left:655px;top:111px;width:2px;height:560px;background:var(--navy)}
.team h2{position:absolute;left:700px;top:118px;font-size:52px;color:var(--navy);font-weight:800;border-bottom:4px solid var(--navy);line-height:58px}
.team p{position:absolute;left:700px;top:205px;width:330px;font-size:18.5px;line-height:33px;color:var(--ink)}
.btn.navyline{border:2px solid var(--navy);color:var(--navy);letter-spacing:1px}

/* appointment */
.appt{top:2964px;left:0;width:1200px;height:590px;background:var(--grey)}
.appt h2{position:absolute;left:460px;top:80px;font-size:40px;color:var(--navy);letter-spacing:1px;font-weight:700}
.field{position:absolute;border:2px solid #9aa1ad;background:transparent;font-size:18px;color:#8a909b;padding:10px 14px}
.hours{position:absolute;left:161px;top:198px;width:241px;height:281px;background:var(--navy);border-radius:28px;color:var(--white);padding:30px 18px;font-size:18px;line-height:30px}
.hours .t{font-family:"Poppins",sans-serif;font-weight:700;text-decoration:underline;font-size:19px}
.hours .u{text-decoration:underline;margin-top:14px}

/* footer */
.footer{top:3541px;left:0;width:1200px;height:467px;background:var(--white)}
.footer .brand{left:160px;top:112px}
.footer .brand .name{font-size:52px}
.footer .brand .sub{font-size:17px;letter-spacing:10px;padding-left:50px}
.socials{position:absolute;left:187px;top:237px;display:flex;gap:30px}
.socials span{width:31px;height:31px;border-radius:50%;background:var(--navy)}
.col h4{font-family:"Poppins",sans-serif;font-weight:600;font-size:22px;color:var(--navy);margin-bottom:22px}
.col{position:absolute;top:130px}
.col .l{font-size:13.5px;color:var(--muted);height:45.5px}
.col .c{font-size:13.5px;color:var(--muted);height:45.5px;display:flex;align-items:flex-start;gap:20px}
.col .c svg{flex:none}
.copy{top:4008px;left:0;width:1200px;height:63px;background:var(--navy);color:var(--white);text-align:center;font-size:14.5px;line-height:63px;letter-spacing:.5px}
</style>
</head>
<body>

<div class="abs topbar">
  <span class="dot" style="left:164px"></span>
  <span class="dot" style="left:202px;border-radius:3px"></span>
  <span class="dot" style="left:242px;border-radius:3px"></span>
  <div class="help">
    <svg width="18" height="18" viewBox="0 0 24 24"><path fill="#fff" d="M6.6 10.8a15 15 0 0 0 6.6 6.6l2.2-2.2c.3-.3.7-.4 1-.2 1.1.4 2.3.6 3.6.6.6 0 1 .4 1 1V20c0 .6-.4 1-1 1A17 17 0 0 1 3 4c0-.6.4-1 1-1h3.5c.6 0 1 .4 1 1 0 1.3.2 2.5.6 3.6.1.3 0 .7-.2 1z"/></svg>
    <span><b>24/7 Help</b>&nbsp; 123 456 7890</span>
  </div>
</div>

<header class="abs header">
  <div class="brand">
    <div class="name">Calder Health</div>
    <div class="sub">SERVICES</div>
  </div>
  <nav class="nav">
    <span>Home</span><span>About Us</span><span>Our Service &#8964;</span><span>Contact</span><span class="search"></span>
  </nav>
</header>

<section class="abs hero" role="img" aria-label="Photo of a nurse resting her hands on the shoulders of a smiling older woman at home">
  <h1 class="heading">Health care for the whole person.</h1>
  <p>Lorem Ipsum is simply dummy text of the printing and typesetting industry. Lorem Ipsum has been the industry's standard dummy text ever since the 1500s.</p>
  <div class="btn teal" style="left:161px;top:429px;width:200px">Make an Appointment</div>
  <div class="btn orange" style="left:410px;top:429px;width:145px">Learn More</div>
</section>
<svg class="edge" style="top:780px" height="30" viewBox="0 0 1200 30" preserveAspectRatio="none"><path fill="#a3dade" d="M0 18 L60 12 L130 16 L210 8 L300 14 L380 10 L470 15 L560 9 L650 13 L740 7 L830 12 L920 8 L1010 14 L1100 9 L1200 12 L1200 30 L0 30Z"/></svg>

<section class="abs welcome">
  <h2 class="heading">WELCOME TO CALDER HEALTH SERVICES</h2>
  <p>Lorem Ipsum Is Simply Dummy Text Of The Printing And Typesetting Industry. Lorem Ipsum Has Been The Industry's Standard Dummy Text Ever Since The 1500s, When An Unknown Printer Took A Galley Of Type And Scrambled It To Make A Type Specimen Book.</p>
</section>

<section class="abs stories" role="img" aria-label="Photo of a young woman hugging an older woman, both smiling">
  <h2 class="heading">Client Success Stories</h2>
  <p>Lorem Ipsum is simply dummy text of the printing and typesetting industry. Lorem Ipsum has been the industry's standard dummy text ever since the 1500s.</p>
  <div class="btn outline" style="left:161px;top:440px;width:146px">CLICK HERE</div>
</section>
<svg class="edge" style="top:1583px" height="34" viewBox="0 0 1200 34" preserveAspectRatio="none"><path fill="#fff" d="M0 20 L70 24 L150 16 L240 22 L330 14 L420 20 L510 12 L600 18 L690 10 L780 17 L870 12 L960 20 L1050 14 L1140 21 L1200 17 L1200 34 L0 34Z"/></svg>

<div class="abs services-title"><h2 class="heading">Services We Offer</h2></div>

<div class="card" style="left:161px">
  <svg class="icon" viewBox="0 0 52 52" fill="none" stroke="#0b1c3d" stroke-width="2"><circle cx="24" cy="22" r="16"/><path d="M24 15v14M17 22h14"/><path d="M30 37v8M14 36v9"/></svg>
  <span class="num">01</span><h3>Behavioral Health</h3>
  <p>Lorem Ipsum is simply dummy text of the printing and typesetting industry. Lorem Ipsum has been the industry's standard dummy text ever since the 1500s.Lorem Ipsum is simply dummy text of the printing and typesetting industry.</p>
  <div class="more">Learn More</div>
</div>
<div class="card" style="left:386px">
  <svg class="icon" viewBox="0 0 52 52" fill="none" stroke="#0b1c3d" stroke-width="2"><circle cx="28" cy="10" r="6"/><path d="M26 18v14M8 36c8 0 12 6 22 6l16-8M8 44h10"/></svg>
  <span class="num">02</span><h3>Human Services</h3>
  <p>Lorem Ipsum is simply dummy text of the printing and typesetting industry. Lorem Ipsum has been the industry's standard dummy text ever since the 1500s.Lorem Ipsum is simply dummy text of the printing and typesetting industry.</p>
  <div class="more" style="top:294px">Learn More</div>
</div>
<div class="card" style="left:609px">
  <svg class="icon" viewBox="0 0 52 52" fill="none" stroke="#0b1c3d" stroke-width="2"><circle cx="26" cy="10" r="6"/><path d="M26 18v16M12 34l14-10 14 10M8 44h36"/></svg>
  <span class="num">03</span><h3>Spiritual Needs</h3>
  <p>Lorem Ipsum is simply dummy text of the printing and typesetting industry. Lorem Ipsum has been the industry's standard dummy text ever since the 1500s.Lorem Ipsum is simply dummy text of the printing and typesetting industry.</p>
  <div class="more" style="top:294px">Learn More</div>
</div>
<div class="card" style="left:833px">
  <svg class="icon" viewBox="0 0 52 52" fill="none" stroke="#0b1c3d" stroke-width="2"><circle cx="30" cy="8" r="5"/><path d="M6 34h40v6H6zM10 40v6M42 40v6M14 30h26"/></svg>
  <span class="num">04</span><h3>Indivisual Therapy</h3>
  <p>Lorem Ipsum is simply dummy text of the printing and typesetting industry. Lorem Ipsum has been the industry's standard dummy text ever since the 1500s.Lorem Ipsum is simply dummy text of the printing and typesetting industry.</p>
  <div class="more" style="top:294px">Learn More</div>
</div>

<section class="abs team">
  <div class="ph" role="img" aria-label="Photo of a nurse and an older woman smiling together" style="left:161px;top:111px;background:linear-gradient(135deg,#c9b8a6,#8fb3b8);border-radius:0 100px 0 100px"></div>
  <div class="ph" role="img" aria-label="Photo of a nurse showing a laptop to an older patient" style="left:385px;top:111px;background:linear-gradient(135deg,#6f95b8,#d8d4cf);border-radius:100px 0 100px 0"></div>
  <div class="ph" role="img" aria-label="Photo of a smiling older woman with a caregiver's hands on her shoulders" style="left:161px;top:332px;background:linear-gradient(135deg,#5b7f99,#c4a58c);border-radius:100px 0 100px 0"></div>
  <div class="ph" role="img" aria-label="Photo of an older woman making a heart shape with her hands outdoors" style="left:382px;top:332px;background:linear-gradient(135deg,#9bb07c,#e5ddd0);border-radius:0 100px 0 100px"></div>
  <div class="divider"></div>
  <h2 class="heading">Our Team</h2>
  <p>Lorem Ipsum is simply dummy text of the printing and typesetting industry. Lorem Ipsum has been the industry's standard dummy text ever since the 1500s, when an unknown printer took a galley of type and scrambled it to make a type specimen book. It has survived not only five centuries, but also the leap into electronic typesetting, remaining essentially unchanged.</p>
  <div class="btn navyline" style="left:700px;top:617px;width:146px">CLICK HERE</div>
</section>
<svg class="edge" style="top:2232px" height="26" viewBox="0 0 1200 26" preserveAspectRatio="none"><path fill="#fff" d="M0 0H1200V8 L1100 14 L1000 6 L900 12 L800 4 L700 10 L600 6 L500 12 L400 8 L300 14 L200 8 L100 16 L0 20Z"/></svg>

<section class="abs appt">
  <h2 class="heading">REQUEST AN APPOINTMENT</h2>
  <div class="hours">
    <div class="t">HOURS &amp; LOCATION</div>
    <div class="u">Washington Dc</div>
    <div style="margin-top:14px">Monday - Friday<br>8.00 a.m. - 4.00 p.m</div>
    <div style="margin-top:16px">Tel: 123 456 7890</div>
  </div>
  <div class="field" style="left:461px;top:174px;width:277px;height:43px">First Name*</div>
  <div class="field" style="left:760px;top:174px;width:277px;height:43px">Last Name*</div>
  <div class="field" style="left:461px;top:255px;width:576px;height:43px">Email Address*</div>
  <div class="field" style="left:461px;top:328px;width:576px;height:43px">Phone Number*</div>
  <div class="field" style="left:461px;top:400px;width:576px;height:96px">Message*</div>
</section>
<svg class="edge" style="top:3528px" height="26" viewBox="0 0 1200 26" preserveAspectRatio="none"><path fill="#fff" d="M0 14 L90 8 L180 14 L270 6 L360 12 L450 5 L540 11 L630 6 L720 13 L810 7 L900 12 L990 5 L1080 11 L1200 7 V26 H0Z"/></svg>

<footer class="abs footer">
  <div class="brand">
    <div class="name">Calder Health</div>
    <div class="sub">SERVICES</div>
  </div>
  <div class="socials"><span></span><span></span><span></span><span style="border-radius:4px"></span></div>
  <div class="col" style="left:536px">
    <h4>Links</h4>
    <div class="l">Home</div><div class="l">About Us</div><div class="l">Our Service</div><div class="l">Insurance</div><div class="l">Contact</div>
  </div>
  <div class="col" style="left:778px">
    <h4>Get In Touch</h4>
    <div class="c"><svg width="20" height="22" viewBox="0 0 24 24"><path fill="#0b1c3d" d="M12 2a7 7 0 0 0-7 7c0 5 7 13 7 13s7-8 7-13a7 7 0 0 0-7-7zm0 9.5A2.5 2.5 0 1 1 12 6.5a2.5 2.5 0 0 1 0 5z"/></svg>Washington Dc</div>
    <div class="c"><svg width="22" height="18" viewBox="0 0 24 18"><path fill="#0b1c3d" d="M0 0h24v18H0zM2 2l10 8 10-8"/><path fill="none" stroke="#fff" stroke-width="1.5" d="M2 2l10 8 10-8"/></svg>info@example.com</div>
    <div class="c"><svg width="20" height="20" viewBox="0 0 24 24"><path fill="#0b1c3d" d="M6.6 10.8a15 15 0 0 0 6.6 6.6l2.2-2.2c.3-.3.7-.4 1-.2 1.1.4 2.3.6 3.6.6.6 0 1 .4 1 1V20c0 .6-.4 1-1 1A17 17 0 0 1 3 4c0-.6.4-1 1-1h3.5c.6 0 1 .4 1 1 0 1.3.2 2.5.6 3.6.1.3 0 .7-.2 1z"/></svg>123 456 7890</div>
    <div class="c"><svg width="24" height="20" viewBox="0 0 24 20"><rect x="0" y="4" width="24" height="16" rx="2" fill="#0b1c3d"/><rect x="5" y="0" width="14" height="6" fill="#0b1c3d"/><rect x="4" y="8" width="6" height="9" fill="#fff"/></svg>123 456 7890</div>
  </div>
</footer>

<div class="abs copy">Copyright &copy; 2025 - Calder Health Services. All Right Reserved</div>

</body>
</html>
```